Simple Recipe eBook

I need the graphic work done for a simple recipe ebook, I have attached all of the required information for it, as well as our company logo. Further company info can be found at velorabix.com

I would like each recipe page to include 2 recipes, each recipe needs to include ingredients, picture, method, and nutritional info.

I would like the style to appear fresh and healthy, with lots of graphics and colours to match.
Please let me know if you need any guidance

Target Market(s)

Females aged from 15-25

Industry/Entity Type

It Company

```html
<!DOCTYPE html>
<html lang="en">
<head>
<meta charset="utf-8">
<title>DOs – Healthy Habits</title>
<link href="https://fonts.googleapis.com/css2?family=Pacifico&family=Gabriela&display=swap" rel="stylesheet">
<style>
  :root {
    --page-bg: #ffffff;
    --panel: #a4c077;
    --band-dark: #8fac62;
    --ink: #1c1c14;
    --title-green: #a4c077;
    --art-yellow: #f3d23a;
    --art-red: #c8102e;
    --art-brown: #6b3a1a;
    --art-green: #2e8b3a;
    --art-peach: #f0d99a;
    --art-shadow: rgba(60, 80, 40, 0.25);
  }
  * { margin: 0; padding: 0; box-sizing: border-box; }
  html, body { width: 1200px; height: 1000px; overflow: hidden; background: var(--page-bg); }
  .page { position: relative; width: 1200px; height: 1000px; }
  .panel {
    position: absolute; left: 250px; top: 26px; width: 708px; height: 943px;
    background: var(--panel); overflow: hidden;
  }
  .title-cap {
    position: absolute; left: 105px; top: -330px; width: 480px; height: 424px;
    border-radius: 50%; background: var(--page-bg);
  }
  .title {
    position: absolute; left: 0; width: 100%; top: 22px; text-align: center;
    font-family: "Pacifico", cursive; font-size: 40px; color: var(--title-green); line-height: 1.2;
  }
  .band { position: absolute; left: 0; width: 692px; }
  .band--dark { background: linear-gradient(90deg, var(--band-dark) 0%, var(--band-dark) 50%, var(--panel) 100%); }
  .tip { position: absolute; color: var(--ink); }
  .tip h2 {
    font-family: "Pacifico", cursive; font-weight: 400; font-size: 19px; line-height: 1.3;
    margin-bottom: 6px; letter-spacing: -0.3px;
  }
  .tip p { font-family: "Gabriela", serif; font-size: 11.3px; line-height: 15px; }
  .art { position: absolute; border-radius: 50%; }
</style>
</head>
<body>
<div class="page">
  <div class="panel">
    <div class="title-cap"></div>
    <div class="title">DOs</div>

    <div class="band band--dark" style="top:121px;height:113px"></div>
    <div class="band band--dark" style="top:361px;height:114px"></div>
    <div class="band band--dark" style="top:592px;height:114px"></div>
    <div class="band band--dark" style="top:814px;height:114px"></div>

    <section class="tip" style="left:68px;top:140px;width:380px">
      <h2>Exercise!</h2>
      <p>Exercise is the key to achieving your goals. Aim for at least 30 minutes of high intensity cardio or weight training each day.</p>
    </section>
    <div class="art" role="img" aria-label="Illustration of a lemon with a sweatband and a dumbbell"
         style="left:495px;top:145px;width:135px;height:80px;border-radius:40px;background:linear-gradient(90deg,var(--art-yellow) 0%,var(--art-yellow) 40%,#d8d8d8 55%,#bdbdbd 100%)"></div>

    <div class="art" role="img" aria-label="Illustration of a chicken drumstick and a calculator"
         style="left:92px;top:255px;width:140px;height:100px;border-radius:30px;background:linear-gradient(90deg,#c4956a 0%,#c4956a 40%,#8c0f35 60%,#8c0f35 100%)"></div>
    <section class="tip" style="left:261px;top:252px;width:385px">
      <h2>Count your calories!</h2>
      <p>To be sure you aren't eating too much you should make sure to count your calories. Download an app like FitLogly to help you keep track on the go. The app will also help decide how many calories you should be consuming per day.</p>
    </section>

    <section class="tip" style="left:68px;top:376px;width:385px">
      <h2>Drink plenty of water!</h2>
      <p>Staying hydrated is important to keep your body functioning at its peak. A glass of water before each meal can help you feel fuller quicker. It also helps flush nasty toxins.</p>
    </section>
    <div class="art" role="img" aria-label="Illustration of glasses of water and a watermelon"
         style="left:485px;top:370px;width:175px;height:115px;border-radius:50px;background:linear-gradient(90deg,#e6f0f5 0%,#e6f0f5 30%,var(--art-green) 50%,var(--art-green) 100%)"></div>

    <div class="art" role="img" aria-label="Illustration of a sleeping mask on a round pillow"
         style="left:119px;top:496px;width:88px;height:88px;background:var(--art-brown)"></div>
    <section class="tip" style="left:261px;top:506px;width:360px">
      <h2>Get a good nights sleep!</h2>
      <p>Your beauty rest is important to help your body repair. <br>6-8 hours every night is recommended.</p>
    </section>

    <section class="tip" style="left:68px;top:610px;width:400px">
      <h2>Write down your goals!</h2>
      <p>Did you know that writing down your goals increases your chance of actually completing them? It does! Give it a go. Write them down and stick to them. Hard work and consistency pays off!</p>
    </section>
    <div class="art" role="img" aria-label="Illustration of a notepad with a checklist, a pen and a slice of bread"
         style="left:478px;top:600px;width:176px;height:100px;border-radius:12px;background:linear-gradient(90deg,#f2f2f2 0%,#f2f2f2 55%,var(--art-peach) 70%,var(--art-peach) 100%)"></div>

    <div class="art" role="img" aria-label="Illustration of a banana, a mushroom and berries"
         style="left:122px;top:722px;width:96px;height:70px;border-radius:35px;background:var(--art-yellow)"></div>
    <section class="tip" style="left:261px;top:730px;width:390px">
      <h2>Eat fruits and veges!</h2>
      <p>Fresh fruit and veges are loaded with healthy vitamins and antioxidants that your body loves!</p>
    </section>

    <section class="tip" style="left:68px;top:834px;width:420px">
      <h2>Do it with a friend!</h2>
      <p>Doing your diet and detox with a friend can be a great way to boost motivation and get results. Keep each other on track and share ideas.</p>
    </section>
    <div class="art" role="img" aria-label="Illustration of a pair of cherries"
         style="left:497px;top:860px;width:70px;height:48px;border-radius:24px;background:var(--art-red)"></div>
  </div>
</div>
</body>
</html>
```